Brightway Carpet and Tile cleaning Business card Design

I need a design that has the same feel as my van.
i would also like a prominent "Review us on Pagelink" somewhere, but not that it makes it look silly.
I would like the card to have a little bit of grey or black in the design as well.

It will need contact details
phone: 0455 817264
email: rkbrightwayclean@mailbox-example.com
website: www.brightwaycarpetandtilecleaning-example.com.au
Pagelink: /brightwaycarpetandtilecleaning

Industry/Entity Type

Business

Contact Information for Business Card

Phone number 0455817264
Email rkbrightwayclean@mailbox-example.com
Website www.brightwaycarpetandtilecleaning-example.com.au
Facebook/brightwaycarpetandtilecleaning

Colors
000000

Requirements
Must have
• Same feel as my van
• I want the card to stand out from the crowd
Nice to have
• Maybe include a tiny bit of a third colour? Grey's,blacks, orange?

```html
<!DOCTYPE html>
<html lang="en">
<head>
<meta charset="utf-8">
<title>Brightway Carpet and Tile cleaning – Business Card</title>
<link href="https://fonts.googleapis.com/css2?family=Roboto:wght@300;400;500&display=swap" rel="stylesheet">
<style>
  :root {
    --backdrop: #bcbcbc;
    --shadow: #8a8a8a;
    --card-white: #ffffff;
    --orange: #f59320;
    --blue: #0daed9;
    --ink: #2e2a26;
    --handle: #7a6450;
    --white: #ffffff;
  }
  * { margin: 0; padding: 0; box-sizing: border-box; }
  html, body {
    width: 1200px; height: 1200px; overflow: hidden;
    background: var(--backdrop);
    font-family: "Roboto", Arial, sans-serif;
  }
  .stage { position: relative; width: 1200px; height: 1200px; }
  .card {
    position: absolute; top: 173px; width: 454px; height: 742px;
    box-shadow: 12px 12px 6px var(--shadow);
    overflow: hidden;
  }
  .card-front { left: 124px; background: var(--card-white); }
  .card-back { left: 622px; background: var(--orange); }

  .brand {
    position: absolute; left: 0; width: 100%;
    display: flex; align-items: center; justify-content: center; gap: 12px;
    color: var(--blue); font-weight: 500;
  }
  .brand-dot { width: 26px; height: 26px; border-radius: 50%; background: var(--blue); flex: none; }
  .brand-text { line-height: 1; text-align: left; }
  .brand-name { display: block; font-size: 50px; letter-spacing: -0.5px; }
  .brand-tagline { display: block; font-size: 15.5px; letter-spacing: 1.6px; text-transform: uppercase; margin-top: 6px; }
  .card-front .brand { top: 330px; }
  .card-back .brand { top: 115px; }

  .accent-band { position: absolute; left: 57px; top: 257px; }

  .contact {
    position: absolute; left: 0; width: 100%;
    text-align: center; color: var(--ink); font-weight: 300;
    white-space: nowrap;
  }
  .contact-phone { top: 327px; font-size: 20px; }
  .contact-email { top: 425px; font-size: 19px; }
  .contact-web { top: 522px; font-size: 15px; letter-spacing: -0.1px; }
  .contact-social { top: 618px; font-size: 19px; color: var(--handle); }

  .rule {
    position: absolute; left: 62px; width: 330px; height: 1.5px;
    background: var(--blue);
  }
  .rule-1 { top: 385px; }
  .rule-2 { top: 488px; }
  .rule-3 { top: 590px; }

  .review-button {
    position: absolute; left: 72px; top: 695px; width: 310px; height: 47px;
    background: var(--blue); color: var(--white);
    font-size: 18.5px; font-weight: 300;
    display: flex; align-items: center; justify-content: center;
  }
</style>
</head>
<body>
<main class="stage">
  <section class="card card-front" aria-label="Card front">
    <div class="brand">
      <span class="brand-dot"></span>
      <span class="brand-text">
        <span class="brand-name">Brightway</span>
        <span class="brand-tagline">Carpet &amp; Tile Cleaning</span>
      </span>
    </div>
  </section>

  <section class="card card-back" aria-label="Card back">
    <div class="brand">
      <span class="brand-dot"></span>
      <span class="brand-text">
        <span class="brand-name">Brightway</span>
        <span class="brand-tagline">Carpet &amp; Tile Cleaning</span>
      </span>
    </div>

    <svg class="accent-band" width="340" height="17" viewBox="0 0 340 17" aria-hidden="true">
      <polygon points="8,0 332,0 340,17 0,17" fill="var(--blue)"/>
    </svg>

    <p class="contact contact-phone">0455 817264</p>
    <span class="rule rule-1"></span>
    <p class="contact contact-email">rkbrightwayclean@mailbox-example.com</p>
    <span class="rule rule-2"></span>
    <p class="contact contact-web">www.brightwaycarpetandtilecleaning-example.com.au</p>
    <span class="rule rule-3"></span>
    <p class="contact contact-social">brightwaycarpetandtilecleaning</p>

    <div class="review-button">Review us on Pagelink</div>
  </section>
</main>
</body>
</html>
```